Harbourline Electrical Solutions

On one side. LOGO (underneath:) Commercial Industrial Residential

- NAME & CONTACT DETAILS

Marcus T. Hollings
Project Manager

(Cell icon) (441) 555-0187
(Email icon) hlelectricalsolutions@mailvento.com
(Facebook & Instagram icons )@hlelectricalsolutions

Other side: LOGO - underneath ELECTRICAL CONSTRUCTION & MAINTENANCE . LED LIGHTING & AUTOMATION . LIFE SAFETY SYSTEMS (FIRE ALARM / SECURITY) . DATA & COMMUNICATION

```html
<!DOCTYPE html>
<html lang="en">
<head>
<meta charset="UTF-8">
<title>Harbourline Electrical Solutions – Business Card</title>
<link href="https://fonts.googleapis.com/css2?family=Montserrat:wght@300;400;500;600;700&display=swap" rel="stylesheet">
<style>
  :root {
    --teal: #10566b;
    --teal-band: #21627a;
    --ink: #2b2b2b;
    --grey: #4a4a4a;
    --white: #ffffff;
    --backdrop: #2a2a2d;
  }
  * { margin: 0; padding: 0; box-sizing: border-box; }
  html, body { width: 1200px; height: 1200px; overflow: hidden; }
  body {
    background: var(--backdrop);
    font-family: "Montserrat", sans-serif;
    position: relative;
  }
  .card {
    position: absolute;
    left: 292px;
    width: 599px;
    height: 360px;
  }
  .card--front { top: 220px; background: var(--teal); color: var(--white); }
  .card--back { top: 632px; background: var(--white); }

  .brand {
    position: absolute;
    display: flex;
    align-items: center;
    gap: 14px;
  }
  .brand__square { width: 22px; height: 22px; }
  .brand__name {
    font-weight: 500;
    letter-spacing: 2.6px;
    line-height: 1.12;
    text-transform: uppercase;
  }
  .card--front .brand { left: 0; right: 0; top: 128px; justify-content: center; }
  .card--front .brand__square { background: var(--white); }
  .card--front .brand__name { font-size: 19px; color: var(--white); }

  .services {
    position: absolute;
    left: 73px;
    top: 302px;
    font-size: 11.3px;
    font-weight: 300;
    line-height: 16px;
    letter-spacing: 0.1px;
  }

  .card--back .brand { left: 0; right: 0; top: 42px; justify-content: center; }
  .card--back .brand__square { background: var(--teal); }
  .card--back .brand__name { font-size: 18px; color: var(--teal); }

  .sectors {
    position: absolute;
    left: 0; right: 0;
    top: 124px;
    text-align: center;
    font-size: 11.5px;
    font-weight: 500;
    letter-spacing: 3px;
    color: var(--ink);
  }
  .sectors__sep { color: var(--teal); margin: 0 4px; }

  .person {
    position: absolute;
    right: 311px;
    top: 280px;
    text-align: right;
  }
  .person__name { font-size: 16px; font-weight: 700; color: var(--teal); letter-spacing: 0.3px; }
  .person__role { font-size: 11px; font-weight: 500; color: var(--ink); margin-top: 2px; }

  .divider {
    position: absolute;
    left: 299px;
    top: 269px;
    width: 1px;
    height: 53px;
    background: var(--teal);
  }

  .contact {
    position: absolute;
    left: 310px;
    top: 270px;
    list-style: none;
    font-size: 11.3px;
    color: var(--grey);
  }
  .contact__item { display: flex; align-items: center; gap: 4px; height: 17.6px; }
  .contact__icon { width: 12px; height: 12px; flex: none; }

  .band {
    position: absolute;
    left: 0; bottom: 0;
    width: 100%;
    height: 18px;
    background: var(--teal-band);
  }
</style>
</head>
<body>
  <section class="card card--front">
    <div class="brand">
      <span class="brand__square"></span>
      <span class="brand__name">Harbourline<br>Electrical<br>Solutions</span>
    </div>
    <p class="services">
      ELECTRICAL CONSTRUCTION &amp; MAINTENANCE • LED LIGHTING &amp; AUTOMATION<br>
      • LIFE SAFETY SYSTEMS (FIRE ALARM / SECURITY) • DATA &amp; COMMUNICATION
    </p>
  </section>

  <section class="card card--back">
    <div class="brand">
      <span class="brand__square"></span>
      <span class="brand__name">Harbourline<br>Electrical<br>Solutions</span>
    </div>
    <p class="sectors">COMMERCIAL <span class="sectors__sep">|</span> INDUSTRIAL <span class="sectors__sep">|</span> RESIDENTIAL</p>

    <div class="person">
      <p class="person__name">MARCUS T. HOLLINGS</p>
      <p class="person__role">Project Manager</p>
    </div>
    <span class="divider"></span>

    <ul class="contact">
      <li class="contact__item">
        <svg class="contact__icon" viewBox="0 0 12 12" aria-hidden="true">
          <circle cx="6" cy="6" r="5.4" fill="none" stroke="#10566b" stroke-width="0.9"/>
          <path d="M4 3.3l1 1.2-.6.7c.4.9 1 1.5 1.9 1.9l.7-.6 1.2 1-.6.9C5.5 8.2 3.8 6.5 3.4 4z" fill="#10566b"/>
        </svg>
        (441) 555-0187
      </li>
      <li class="contact__item">
        <svg class="contact__icon" viewBox="0 0 12 12" aria-hidden="true">
          <circle cx="6" cy="6" r="5.4" fill="none" stroke="#10566b" stroke-width="0.9"/>
          <rect x="3.3" y="4" width="5.4" height="4" fill="none" stroke="#10566b" stroke-width="0.8"/>
          <path d="M3.3 4l2.7 2.2L8.7 4" fill="none" stroke="#10566b" stroke-width="0.8"/>
        </svg>
        hlelectricalsolutions@mailvento.com
      </li>
      <li class="contact__item">
        <svg class="contact__icon" viewBox="0 0 12 12" aria-hidden="true">
          <circle cx="6" cy="6" r="5.4" fill="none" stroke="#10566b" stroke-width="0.9"/>
        </svg>
        <svg class="contact__icon" viewBox="0 0 12 12" aria-hidden="true" style="margin-left:5px">
          <circle cx="6" cy="6" r="5.4" fill="none" stroke="#10566b" stroke-width="0.9"/>
        </svg>
        <span style="margin-left:2px">@hlelectricalsolutions</span>
      </li>
    </ul>

    <span class="band"></span>
  </section>
</body>
</html>
```